Business Cards - Brightpath Horizon

need to design unique business card for my mortgage business. I need to design credit card style business card for my business or any unique idea that you might have

Target Market(s)

Home Loan customers

Industry/Entity Type

Mortgage Brokerage

Contact Information for Business Card

please design credit card style or very unique style business card

Colors

Designer to choose colors to be used in the design.

Requirements
Must have
• Name
• position
• Phone number
• fax number
• email address
• website address
• social media address
• All above fields will be provided once design in finalised

```html
<!DOCTYPE html>
<html lang="en">
<head>
<meta charset="utf-8">
<title>Brightpath Horizon – Business Cards</title>
<link href="https://fonts.googleapis.com/css2?family=Poppins:wght@400;500;600&display=swap" rel="stylesheet">
<style>
  :root {
    --backdrop: #3b3732;
    --royal-blue: #3550a8;
    --sky-blue: #2aa3dc;
    --accent-orange: #f28a1e;
    --card-white: #ffffff;
    --ink: #3a3a3a;
  }
  html, body {
    margin: 0;
    padding: 0;
    width: 1200px;
    height: 930px;
    overflow: hidden;
    background: var(--backdrop);
    font-family: "Poppins", sans-serif;
  }
  .canvas {
    position: relative;
    width: 1200px;
    height: 930px;
  }
  .card {
    position: absolute;
    width: 520px;
    height: 328px;
    border-radius: 18px;
    overflow: hidden;
    box-shadow: 0 10px 24px rgba(0,0,0,0.35);
  }
  /* Front */
  .card-front {
    left: 90px;
    top: 110px;
    background: var(--royal-blue);
    color: var(--card-white);
  }
  .card-front .brand-name {
    position: absolute;
    left: 0;
    right: 0;
    top: 128px;
    text-align: center;
    font-size: 34px;
    font-weight: 600;
    letter-spacing: 0.5px;
    color: var(--card-white);
  }
  .card-front .web-address {
    position: absolute;
    left: 0;
    right: 0;
    bottom: 36px;
    text-align: center;
    font-size: 13px;
    letter-spacing: 1.5px;
    color: var(--card-white);
  }
  /* Back */
  .card-back {
    left: 590px;
    top: 490px;
    background: var(--card-white);
  }
  .card-back .wave {
    position: absolute;
    left: 0;
    top: 0;
    width: 520px;
    height: 328px;
  }
  .card-back .brand-name {
    position: absolute;
    left: 30px;
    top: 112px;
    width: 220px;
    font-size: 27px;
    line-height: 1.15;
    font-weight: 600;
    color: var(--royal-blue);
  }
  .card-back .divider {
    position: absolute;
    left: 268px;
    top: 58px;
    width: 1.5px;
    height: 150px;
    background: var(--royal-blue);
  }
  .details {
    position: absolute;
    left: 290px;
    top: 54px;
    color: var(--ink);
  }
  .details .person-name {
    margin: 0;
    font-size: 19px;
    font-weight: 500;
    letter-spacing: 1.5px;
    color: var(--sky-blue);
    text-transform: uppercase;
  }
  .details .person-role {
    margin: 2px 0 12px;
    font-size: 12px;
    font-weight: 600;
  }
  .details .address {
    margin: 0 0 12px;
    font-size: 10.5px;
    line-height: 1.35;
  }
  .contact-list {
    list-style: none;
    margin: 0;
    padding: 0;
    font-size: 10.5px;
    line-height: 1.45;
  }
  .contact-list li {
    display: flex;
    align-items: center;
    gap: 7px;
  }
  .contact-list svg {
    width: 9px;
    height: 9px;
    flex: none;
  }
</style>
</head>
<body>
<main class="canvas">

  <section class="card card-front" aria-label="Business card front">
    <div class="brand-name">Brightpath Horizon</div>
    <div class="web-address">www.yourwebsite.com</div>
  </section>

  <section class="card card-back" aria-label="Business card back">
    <svg class="wave" viewBox="0 0 520 328" aria-hidden="true">
      <defs>
        <linearGradient id="swoosh-line" gradientUnits="userSpaceOnUse" x1="0" y1="0" x2="520" y2="0">
          <stop offset="0" stop-color="var(--accent-orange)"/>
          <stop offset="0.42" stop-color="var(--accent-orange)"/>
          <stop offset="0.62" stop-color="var(--sky-blue)"/>
          <stop offset="1" stop-color="var(--sky-blue)"/>
        </linearGradient>
      </defs>
      <path d="M0,328 L0,308 C160,276 340,262 520,206 L520,328 Z" fill="var(--royal-blue)"/>
      <path d="M0,298 C160,266 340,252 520,195" fill="none" stroke="url(#swoosh-line)" stroke-width="4"/>
    </svg>

    <div class="brand-name">Brightpath Horizon</div>
    <div class="divider"></div>

    <div class="details">
      <h1 class="person-name">Daniel Porter</h1>
      <p class="person-role">Founder</p>
      <p class="address">450 Harbor View Ave.<br>Coral Bay, FL 33100</p>
      <ul class="contact-list">
        <li>
          <svg viewBox="0 0 10 10" aria-hidden="true"><path d="M2,1 L4,1 L4.6,3 L3.4,3.8 C4,5 5,6 6.2,6.6 L7,5.4 L9,6 L9,8 C5,8.5 1.5,5 2,1 Z" fill="var(--sky-blue)"/></svg>
          555-014-2290
        </li>
        <li>
          <svg viewBox="0 0 10 10" aria-hidden="true"><rect x="0.8" y="2" width="8.4" height="6" fill="none" stroke="var(--sky-blue)" stroke-width="1.2"/><path d="M1,2.4 L5,5.4 L9,2.4" fill="none" stroke="var(--sky-blue)" stroke-width="1.2"/></svg>
          hello@brightpathhorizon.com
        </li>
        <li>
          <svg viewBox="0 0 10 10" aria-hidden="true"><circle cx="5" cy="5" r="4" fill="none" stroke="var(--sky-blue)" stroke-width="1.1"/><ellipse cx="5" cy="5" rx="1.7" ry="4" fill="none" stroke="var(--sky-blue)" stroke-width="0.9"/><line x1="1" y1="5" x2="9" y2="5" stroke="var(--sky-blue)" stroke-width="0.9"/></svg>
          www.brightpathhorizon.com
        </li>
      </ul>
    </div>
  </section>

</main>
</body>
</html>
```